Vantor Wear and Fuel is looking for a Clothing/Supplement Online Store Website!

Must be convenient, and user friendly, with vibrant colors that catch the eye!

Target Market(s)

Athletes, and Fashion Customers

Industry/Entity Type

Fitness

Coding

Coded - Design and coding required

Number of Pages Required

3 page

Font styles to use
Decorative

Colors

Designer to choose colors to be used in the design.

Requirements
Must have
• Somewhere to feature products, features to promote discounts and make announcements.
Nice to have
• My logos on each page

```html
<!DOCTYPE html>
<html lang="en">
<head>
<meta charset="utf-8">
<title>Vantor Wear and Fuel – Athletes Clothes &amp; Supplement</title>
<link rel="stylesheet" href="https://fonts.googleapis.com/css2?family=Montserrat:wght@400;500;600;700;800&family=Poppins:wght@300;400;500&display=swap">
<style>
:root{
  --orange:#f7941d;
  --ink:#1e1e20;
  --text:#333336;
  --muted:#8a8a8e;
  --soft:#f7f7f8;
  --line:#e4e4e6;
  --white:#ffffff;
  --dark:#161617;
}
*{box-sizing:border-box;margin:0;padding:0}
html,body{width:1200px;height:4124px;overflow:hidden}
body{position:relative;background:var(--white);font-family:"Poppins",sans-serif;color:var(--text)}
.abs{position:absolute}
.head{font-family:"Montserrat",sans-serif}
.btn{position:absolute;display:flex;align-items:center;justify-content:center;border-radius:20px;background:var(--orange);color:var(--white);font-family:"Montserrat",sans-serif;font-weight:600;font-size:12px;letter-spacing:.3px}
.btn.dark{background:var(--ink)}
.section-title{position:absolute;left:0;width:1200px;text-align:center;font-family:"Montserrat",sans-serif;font-weight:800;font-size:35px;color:var(--ink);letter-spacing:.5px}
.section-title span{color:var(--orange)}

/* top bar */
.topbar{top:0;left:0;width:1200px;height:78px;border-top:3px solid var(--orange)}
.top-contact{top:22px;display:flex;align-items:center;gap:14px;font-size:12px;color:var(--text);white-space:nowrap}
.brand-name{top:22px;left:0;width:1200px;text-align:center;font-family:"Montserrat",sans-serif;font-weight:700;font-size:26px;color:var(--ink);letter-spacing:1px}
.nav{top:78px;left:0;width:1200px;height:42px;border-top:1px solid var(--line)}
.nav a{position:absolute;top:14px;font-family:"Montserrat",sans-serif;font-size:11.5px;font-weight:500;color:var(--text);text-decoration:none;transform:translateX(-50%);white-space:nowrap}
.nav a.active{color:var(--orange)}
.nav i{position:absolute;top:12px;width:1px;height:18px;background:var(--line)}

/* hero */
.hero-photo{top:120px;left:0;width:1200px;height:520px;background:linear-gradient(100deg,#7d6d56 0%,#b9a78f 22%,#d9d8d6 45%,#eceded 70%,#f2f3f4 100%)}
.hero-title{top:268px;right:144px;text-align:right;font-family:"Montserrat",sans-serif;font-weight:700;font-size:50px;line-height:64px;color:var(--ink);white-space:nowrap}
.hero-sub{top:396px;right:144px;font-size:12px;color:var(--orange);white-space:nowrap}

/* about */
.about-title{top:672px;left:640px;font-family:"Montserrat",sans-serif;font-weight:800;font-size:36px;color:var(--ink)}
.about-title span{color:var(--orange)}
.about-sub{top:727px;left:638px;font-family:"Montserrat",sans-serif;font-weight:500;font-size:15px;color:var(--orange);white-space:nowrap}
.about-copy{left:635px;width:421px;font-size:11px;line-height:20.5px;color:var(--muted);text-align:justify}

/* products */
.products-bg{top:1155px;left:0;width:1200px;height:853px;background:var(--soft)}
.product-card{position:absolute;width:260px;height:294px;background:var(--white);padding:9px;box-shadow:0 0 0 1px #eeeeef}
.product-card .inner{width:100%;height:100%;border:1px solid #d9d9dc;position:relative}
.product-card .pic{position:absolute;left:50%;transform:translateX(-50%);top:18px;width:170px;height:190px;border-radius:10px}
.product-card .label{position:absolute;bottom:26px;left:0;width:100%;text-align:center;font-family:"Montserrat",sans-serif;font-weight:500;font-size:15px;color:var(--text)}

/* discounts */
.discount-bg{top:2008px;left:0;width:1200px;height:496px;background:linear-gradient(180deg,#232325,#111112)}
.promo{position:absolute;top:2186px;width:438px;height:310px;background:var(--white);padding:9px}
.promo .inner{position:relative;width:100%;height:100%;overflow:hidden}
.promo .pic{position:absolute;inset:0}
.promo h3{position:absolute;left:29px;top:64px;font-family:"Montserrat",sans-serif;font-weight:800;font-size:31px;color:var(--white);white-space:nowrap}
.promo .off{position:absolute;left:29px;top:104px;font-family:"Montserrat",sans-serif;font-weight:800;font-size:36px;color:var(--orange)}
.promo .off small{font-size:20px}
.promo p{position:absolute;left:29px;top:150px;font-size:14px;color:var(--white)}
.promo .btn{left:29px;top:186px;width:114px;height:32px;font-size:11px}

/* blog */
.blog-card{position:absolute;top:2656px;width:295px;height:349px;background:var(--white);box-shadow:0 3px 10px rgba(0,0,0,.08)}
.blog-card .pic{width:100%;height:240px}
.blog-card .date{position:absolute;top:266px;width:100%;text-align:center;font-size:12px;color:var(--muted)}
.blog-card .date.hot{color:var(--orange)}
.blog-card h4{position:absolute;top:290px;width:100%;text-align:center;font-family:"Montserrat",sans-serif;font-weight:600;font-size:15px;line-height:19px;color:var(--ink)}

/* testimonials */
.testi-bg{top:3144px;left:0;width:1200px;height:600px;background:var(--soft)}
.testi-card{top:3413px;left:304px;width:592px;height:187px;background:var(--white);box-shadow:0 0 12px rgba(0,0,0,.05);text-align:center}
.testi-card h5{margin-top:20px;font-family:"Montserrat",sans-serif;font-weight:600;font-size:16px;color:var(--ink);letter-spacing:.5px}
.testi-card .role{font-size:12px;color:var(--text);margin-top:2px}
.testi-card p{margin:12px auto 0;width:540px;font-size:11.5px;line-height:20px;color:var(--muted)}
.arrow{position:absolute;top:3467px;width:26px;height:26px;border-radius:50%;display:flex;align-items:center;justify-content:center}

/* footer */
.footer-h{top:3850px;font-family:"Montserrat",sans-serif;font-weight:600;font-size:13.5px;color:var(--white);letter-spacing:.3px;white-space:nowrap}
.footer-list{top:3880px;left:141px;list-style:none;font-size:12px;line-height:21.6px;color:var(--white)}
.footer-list li::before{content:"› ";}
.contact-item{left:342px;display:flex;gap:12px;font-size:11.5px;line-height:17px;color:var(--white);white-space:nowrap}
.ring{flex:none;width:26px;height:26px;border:1.5px solid var(--white);border-radius:50%;display:flex;align-items:center;justify-content:center}
.follow-item{left:650px;display:flex;align-items:center;gap:12px;font-size:12px;color:var(--white)}
.follow-item .ring{width:20px;height:20px;border-width:1.3px}
.follow-item .ring i{width:6px;height:6px;background:var(--white);border-radius:50%}
.newsletter-text{top:3892px;left:838px;width:230px;font-size:12px;line-height:20px;color:var(--white)}
.email-field{top:3949px;left:838px;width:205px;height:35px;border:1px solid #8b8b8d;font-size:10.5px;color:#8b8b8d;padding:10px 12px}
.copyright{top:4077px;left:0;width:1200px;height:47px;background:var(--orange);color:var(--white);font-size:11.5px;display:flex;align-items:center;justify-content:center}
.vdiv{position:absolute;top:3855px;width:1px;height:190px;background:#2e2e30}
</style>
</head>
<body>

<!-- Top bar -->
<header class="abs topbar">
  <div class="abs top-contact" style="left:144px">
    <svg width="30" height="34" viewBox="0 0 30 34"><polygon points="15,0 30,8.5 30,25.5 15,34 0,25.5 0,8.5" fill="var(--orange)"/><path d="M10 11c1-1 2-1 2.5 0l1.2 2.2c.4.8 0 1.4-.6 1.9.8 1.8 2 3 3.8 3.8.5-.6 1.1-1 1.9-.6l2.2 1.2c1 .5 1 1.5 0 2.5-1.5 1.5-4 1-7-2s-5-6-4-9z" fill="#fff"/></svg>
    <span>Call Us Today : (555) 208 3140</span>
  </div>
  <div class="abs brand-name">VANTOR</div>
  <div class="abs top-contact" style="left:842px">
    <svg width="30" height="34" viewBox="0 0 30 34"><polygon points="15,0 30,8.5 30,25.5 15,34 0,25.5 0,8.5" fill="var(--orange)"/><rect x="8" y="12" width="14" height="10" rx="1" fill="#fff"/><path d="M8 12l7 6 7-6" stroke="var(--orange)" stroke-width="1.4" fill="none"/></svg>
    <span>Email: info@vantorwear.com</span>
  </div>
</header>

<nav class="abs nav">
  <a class="active" style="left:187px">HOME</a><i style="left:246px"></i>
  <a style="left:309px">ABOUT US</a><i style="left:372px"></i>
  <a style="left:442px">PRODUCT</a><i style="left:514px"></i>
  <a style="left:573px">CLOTHES</a><i style="left:637px"></i>
  <a style="left:704px">SUPPLEMENT</a><i style="left:782px"></i>
  <a style="left:835px">BLOG</a><i style="left:888px"></i>
  <a style="left:963px">CONTACT US</a>
</nav>

<!-- Hero -->
<div class="abs hero-photo" role="img" aria-label="Photo of a woman in sportswear sitting on white stone steps with a gym bag"></div>
<h1 class="abs hero-title">ATHLETES CLOTHES<br>&amp; SUPPLEMENT</h1>
<div class="abs hero-sub">Vantor Fitness Clothing  Supplement Online Store</div>
<div class="btn" style="left:946px;top:435px;width:112px;height:32px">SHOP NOW</div>
<svg class="abs" style="top:555px;left:0" width="1200" height="90" viewBox="0 0 1200 90">
  <polygon points="0,70 560,30 600,24 640,30 1200,76 1200,90 0,90" fill="#fff"/>
  <polyline points="0,70 570,29 630,29 1200,76" fill="none" stroke="var(--orange)" stroke-width="5"/>
  <polygon points="572,14 628,14 628,30 600,48 572,30" fill="#fff"/>
  <path d="M600 19v18M594 31l6 6 6-6" stroke="var(--orange)" stroke-width="2" fill="none"/>
</svg>

<!-- About -->
<svg class="abs" style="top:645px;left:120px" width="500" height="470" viewBox="0 0 500 470">
  <polygon points="211,5 378,100 378,290 211,385 44,290 44,100" fill="none" stroke="#f1f1f2" stroke-width="26"/>
  <g role="img" aria-label="Photo of a woman in a grey hoodie and leggings against a dark wall">
    <polygon points="211,75 343,151 343,303 211,379 79,303 79,151" fill="#6f6f70"/>
  </g>
  <g role="img" aria-label="Photo of a smiling woman in a gym holding a supplement tub">
    <polygon points="371,196 482,260 482,388 371,452 260,388 260,260" fill="#2a2a2c" stroke="#fff" stroke-width="8"/>
  </g>
</svg>
<h2 class="abs about-title">ABOUT <span>US</span></h2>
<div class="abs about-sub">WELCOME TO VANTOR WEAR AND FUEL</div>
<p class="abs about-copy" style="top:760px">Lorem ipsum dolor sit amet, consectetuer adipiscing elit, sed diam nonummy nibh euismod tincidunt ut laoreet dolore magna aliquam erat volutpat. Ut wisi enim ad minim veniam, quis nostrud exerci tation ullamcorper suscipit lobortis nisl ut aliquip ex ea commodo consequat. Duis autem vel eum iriure dolor in hendrerit in vulputate velit esse molestie consequat, vel illum dolore eu feugiat nulla facilisis at vero eros et accumsan et iusto odio dignissim qui blandit praesent luptatum</p>
<p class="abs about-copy" style="top:906px">Lorem ipsum dolor sit amet, consectetuer adipiscing elit, sed diam nonummy nibh euismod tincidunt ut laoreet dolore magna aliquam erat volutpat. Ut wisi enim ad minim veniam, quis nostrud exerci tation ullamcorper suscipit lobortis nisl ut aliquip ex ea commodo consequat. Duis autem vel eum iriure dolor in hendrerit in vulputate</p>
<div class="btn" style="left:635px;top:1050px;width:112px;height:33px">READ MORE</div>

<!-- Featured products -->
<div class="abs products-bg"></div>
<h2 class="section-title" style="top:1215px">FEATURE <span>PRODUCTS</span></h2>

<div class="product-card" style="left:141px;top:1308px"><div class="inner">
  <div class="pic" role="img" aria-label="Lime green fitness tank top" style="background:linear-gradient(180deg,#c6ef3a,#9ccc1f)"></div>
  <div class="label">Fitness Tank Top</div></div></div>
<div class="product-card" style="left:466px;top:1308px"><div class="inner">
  <div class="pic" role="img" aria-label="Supplement tubs with a kettlebell" style="background:linear-gradient(160deg,#3a7a3c,#1e1f22 65%,#8b8e95)"></div>
  <div class="label">Fitness  Supplement</div></div></div>
<div class="product-card" style="left:790px;top:1308px"><div class="inner">
  <div class="pic" role="img" aria-label="Blue and white basketball jersey" style="background:linear-gradient(90deg,#1f3f8f,#e8ecf4 50%,#1f3f8f)"></div>
  <div class="label">Fitness Tank Top</div></div></div>

<div class="product-card" style="left:141px;top:1633px"><div class="inner">
  <div class="pic" role="img" aria-label="Chrome dumbbells with a supplement bottle" style="background:linear-gradient(150deg,#d5d7da,#8d9095 55%,#1d2a45)"></div>
  <div class="label">Fitness  Supplement</div></div></div>
<div class="product-card" style="left:466px;top:1633px"><div class="inner">
  <div class="pic" role="img" aria-label="Red and black sports jersey" style="background:linear-gradient(160deg,#c02027,#2a1a1b 60%,#b51d24)"></div>
  <div class="label">Fitness Tank Top</div></div></div>
<div class="product-card" style="left:790px;top:1633px"><div class="inner">
  <div class="pic" role="img" aria-label="Black compression shorts" style="background:linear-gradient(180deg,#2b2e3a,#111217)"></div>
  <div class="label">Fitness Tank Top</div></div></div>

<!-- Discounts -->
<div class="abs discount-bg" role="img" aria-label="Dark gym background photo"></div>
<h2 class="section-title" style="top:2100px;color:var(--white)">PROMOTE <span>DISCOUNTS</span></h2>
<svg class="abs" style="top:2420px;left:0" width="1200" height="90" viewBox="0 0 1200 90">
  <polygon points="0,84 150,62 150,90 0,90" fill="#fff"/>
  <polygon points="1050,62 1200,84 1200,90 1050,90" fill="#fff"/>
  <rect x="150" y="76" width="900" height="14" fill="#fff"/>
  <polyline points="0,80 150,58" stroke="var(--orange)" stroke-width="5" fill="none"/>
  <polyline points="1050,58 1200,80" stroke="var(--orange)" stroke-width="5" fill="none"/>
  <rect x="578" y="15" width="43" height="10" fill="var(--orange)"/>
  <polygon points="578,25 621,25 621,90 578,90" fill="#fff"/>
</svg>
<div class="promo" style="left:141px"><div class="inner">
  <div class="pic" role="img" aria-label="Photo of a woman in an orange sports top against a grey wall" style="background:linear-gradient(90deg,#3b3d44 0%,#4d5058 55%,#6a6c72 100%)"></div>
  <h3>Big Discount</h3><div class="off">-30% <small>OFF</small></div>
  <p>Fitness Clothes Fashion</p><div class="btn">SHOP NOW</div></div></div>
<div class="promo" style="left:621px"><div class="inner">
  <div class="pic" role="img" aria-label="Photo of a man in a red sports shirt holding a supplement tub" style="background:linear-gradient(90deg,#0c0c0d 0%,#151516 50%,#3b1512 80%,#0c0c0d 100%)"></div>
  <h3>Big Discount</h3><div class="off">-20% <small>OFF</small></div>
  <p>Fitness Supplement</p><div class="btn">SHOP NOW</div></div></div>

<!-- Blog -->
<h2 class="section-title" style="top:2570px">LATEST <span>BLOG</span></h2>
<article class="blog-card" style="left:141px">
  <div class="pic" role="img" aria-label="Photo of a man resting in a gym with a water bottle" style="background:linear-gradient(180deg,#9a9c9a,#cfd0cd)"></div>
  <div class="date">27,Ocoober 2019</div><h4>Lorem Ipsum Dolor Sit Amet,<br>Adipiscing Elit</h4></article>
<article class="blog-card" style="left:453px">
  <div class="pic" role="img" aria-label="Photo of a woman in a pink jacket drinking water on steps" style="background:linear-gradient(180deg,#c89b64,#8a6a4c)"></div>
  <div class="date hot">27,Ocoober 2019</div><h4>Lorem Ipsum Dolor Sit Amet,<br>Adipiscing Elit</h4></article>
<article class="blog-card" style="left:763px">
  <div class="pic" role="img" aria-label="Photo of a fit woman in a white sports bra on a dark background" style="background:linear-gradient(180deg,#3e4a58,#2a323c)"></div>
  <div class="date">27,Ocoober 2019</div><h4>Lorem Ipsum Dolor Sit Amet,<br>Adipiscing Elit</h4></article>
<div class="btn" style="left:544px;top:3048px;width:112px;height:32px">VIEW ALL</div>

<!-- Testimonials -->
<div class="abs testi-bg"></div>
<h2 class="section-title" style="top:3218px">CUSTOMER <span>TESTIMONIALS</span></h2>
<div class="abs" role="img" aria-label="Customer portrait" style="top:3312px;left:552px;width:96px;height:96px;border-radius:50%;background:linear-gradient(180deg,#5c5048,#2a2624)"></div>
<div class="abs testi-card">
  <h5>JOHN DOE</h5><div class="role">Lorem ipsum</div>
  <p>Lorem ipsum dolor sit amet, consectetuer adipiscing elit, sed diam nonummy nibh euismod tincidunt ut laoreet dolore magna aliquam erat volutpat. Ut wisi enim ad minim veniam, quis nostrud.Lorem ipsum dolor sit amet, consectetuer adipiscing elit, sed diam nonummy nibh euismod tincidunt ut laoreet dolore magna aliquam erat volutpat.</p>
</div>
<div class="arrow" style="left:142px;background:var(--ink)"><svg width="10" height="10" viewBox="0 0 10 10"><path d="M6.5 1.5L3 5l3.5 3.5" stroke="#fff" stroke-width="1.6" fill="none"/></svg></div>
<div class="arrow" style="left:1032px;background:var(--orange)"><svg width="10" height="10" viewBox="0 0 10 10"><path d="M3.5 1.5L7 5 3.5 8.5" stroke="#fff" stroke-width="1.6" fill="none"/></svg></div>

<!-- Footer -->
<svg class="abs" style="top:3630px;left:0" width="1200" height="447" viewBox="0 0 1200 447">
  <polygon points="0,16 545,98 655,98 1200,20 1200,447 0,447" fill="var(--dark)"/>
  <polyline points="0,12 545,94 655,94 1200,16" stroke="var(--orange)" stroke-width="5" fill="none"/>
  <polygon points="600,100 660,128 660,182 600,210 540,182 540,128" fill="#fff"/>
</svg>
<div class="btn dark" style="left:547px;top:3633px;width:106px;height:31px">VIEW ALL</div>
<div class="abs head" style="top:3770px;left:540px;width:120px;text-align:center;font-weight:700;font-size:18px;color:var(--ink);letter-spacing:.5px">VANTOR</div>

<div class="abs footer-h" style="left:141px">QUICK LINK</div>
<ul class="abs footer-list">
  <li>Home</li><li>AboutUs</li><li>Products</li><li>Clothes</li><li>Spplment</li><li>Blog</li><li>Contact Us</li>
</ul>
<span class="vdiv" style="left:280px"></span>

<div class="abs footer-h" style="left:342px">CONTACT DETAILS</div>
<div class="abs contact-item" style="top:3872px">
  <span class="ring"><svg width="10" height="13" viewBox="0 0 10 13"><path d="M5 12S1 7.5 1 4.8a4 4 0 018 0C9 7.5 5 12 5 12z" fill="none" stroke="#fff" stroke-width="1.3"/><circle cx="5" cy="4.8" r="1.3" fill="#fff"/></svg></span>
  <span>Address:<br>48 Harbor Lane Suite 12,<br>Ridgefield 20417</span></div>
<div class="abs contact-item" style="top:3955px">
  <span class="ring"><svg width="12" height="12" viewBox="0 0 12 12"><path d="M2.5 1.5c.6-.6 1.2-.6 1.5 0l.8 1.4c.3.5 0 .9-.4 1.2.5 1.1 1.3 1.9 2.4 2.4.3-.4.7-.7 1.2-.4l1.4.8c.6.3.6.9 0 1.5-1 1-2.6.7-4.5-1.2S1.5 2.5 2.5 1.5z" fill="#fff"/></svg></span>
  <span>Phone:<br>555-208-3140</span></div>
<div class="abs contact-item" style="top:4010px">
  <span class="ring"><svg width="12" height="10" viewBox="0 0 12 10"><rect x="1" y="1" width="10" height="8" rx="1" fill="none" stroke="#fff" stroke-width="1.2"/><path d="M1 1.5l5 4 5-4" stroke="#fff" stroke-width="1.2" fill="none"/></svg></span>
  <span>Email:<br>info@vantorfuel.com</span></div>
<span class="vdiv" style="left:596px"></span>

<div class="abs footer-h" style="left:659px">FOLLOW US</div>
<div class="abs follow-item" style="top:3896px"><span class="ring"><i></i></span>Friendbook</div>
<div class="abs follow-item" style="top:3932px"><span class="ring"><i></i></span>Chirpline</div>
<div class="abs follow-item" style="top:3969px"><span class="ring"><i></i></span>Viewcast</div>
<div class="abs follow-item" style="top:4006px"><span class="ring"><i></i></span>Snapframe</div>
<span class="vdiv" style="left:808px"></span>

<div class="abs footer-h" style="left:840px">JOIN OUR NEWSLETTER NOW</div>
<p class="abs newsletter-text">Get E-mail updates about our latest offers.</p>
<div class="abs email-field">Email Address</div>
<div class="btn" style="left:838px;top:4008px;width:106px;height:30px;font-size:13px">SUBMIT</div>

<div class="abs copyright">Copyright © 2019 Vantor Wear and Fuel. All Rights Reserved.</div>

</body>
</html>
```